Quorva - corporate Business Card

We need a good look and innovative business card for a new start up company based in Los Angeles called "Quorva". We are in a payment business, including payment card, app, and ewallet. We are expert in online payment and Card not present (CNP) transaction.
We need an innovative, modern business card.

Our logo font is Aero Matics

Target Market(s)

Startup - Bank - Online Payment - Card Manufacturing

Industry/Entity Type

Startup

Contact Information for Business Card

phone: 555 014 7396 - Address: 4172 Marlowe blvd, Cylver City, CA 90299

Requirements
Must have
• Message: innovative, professional, expert, high tech, trust, online payment expert, security
Nice to have
• no comment
Should not have
• no Comment

```html
<!DOCTYPE html>
<html lang="en">
<head>
<meta charset="utf-8">
<title>Quorva – Business Card</title>
<link rel="stylesheet" href="https://fonts.googleapis.com/css2?family=Open+Sans:wght@400;600;700&display=swap">
<style>
  :root {
    --page-bg: #d9d9d9;
    --card-dark: #3a3a3b;
    --card-darker: #2b2b2c;
    --band: #1f1f20;
    --brand-red: #c8202f;
    --text-light: #e6e6e6;
    --text-grey: #bdbdbd;
    --divider: #8a8a8a;
  }
  * { margin: 0; padding: 0; box-sizing: border-box; }
  html, body { width: 1200px; height: 1000px; overflow: hidden; }
  body {
    background: var(--page-bg);
    font-family: "Open Sans", Arial, sans-serif;
    position: relative;
  }
  .card {
    position: absolute;
    left: 290px;
    width: 620px;
    height: 354px;
    border-bottom: 4px solid var(--brand-red);
    overflow: hidden;
    box-shadow: 0 10px 24px rgba(0,0,0,0.25);
  }
  /* Back side */
  .card--back { top: 90px; background: var(--card-darker); }
  .pattern-area {
    position: absolute;
    left: 0; width: 100%;
    background: linear-gradient(110deg, #8c8c8c 0%, #4a4a4b 30%, #2f2f30 65%, #262627 100%);
  }
  .pattern-area--top { top: 0; height: 112px; }
  .pattern-area--bottom {
    bottom: 0; height: 128px;
    background: linear-gradient(110deg, #333334 0%, #2c2c2d 60%, #242425 100%);
  }
  .brand-band {
    position: absolute;
    top: 112px; left: 0; width: 100%; height: 114px;
    background: linear-gradient(180deg, var(--band), #2a2a2b);
    display: flex; align-items: center; justify-content: center; gap: 18px;
  }
  .brand-dot { width: 76px; height: 76px; border-radius: 50%; background: var(--brand-red); }
  .brand-name {
    color: var(--brand-red);
    font-weight: 600;
    font-size: 58px;
    letter-spacing: 2px;
    line-height: 1;
  }
  /* Front side */
  .card--front { top: 520px; background: var(--card-dark); }
  .card--front .brand {
    position: absolute; top: 38px; left: 96px;
    display: flex; align-items: center; gap: 22px;
  }
  .card--front .brand-dot { width: 110px; height: 110px; }
  .card--front .brand-name { font-size: 78px; letter-spacing: 4px; }
  .person {
    position: absolute; top: 212px; right: 372px; text-align: right;
  }
  .person__name {
    color: var(--brand-red); font-weight: 700; font-size: 23px; letter-spacing: 1px;
  }
  .person__role {
    color: var(--text-grey); font-weight: 600; font-size: 18px; letter-spacing: 0.5px;
  }
  .divider {
    position: absolute; top: 198px; left: 266px;
    width: 1px; height: 118px; background: var(--divider);
  }
  .contact {
    position: absolute; top: 198px; left: 284px;
    color: var(--text-light); font-size: 16px; line-height: 1.25;
  }
  .contact__address { margin-bottom: 10px; }
  .contact__list { list-style: none; }
  .contact__list li { display: flex; align-items: center; gap: 14px; height: 22px; }
  .contact__list svg { width: 13px; height: 13px; fill: var(--brand-red); flex: none; }
  .accent { color: var(--brand-red); }
</style>
</head>
<body>

<section class="card card--back" aria-label="Card back">
  <div class="pattern-area pattern-area--top" role="img" aria-label="Repeating pattern of small circular brand marks fading from silver to black"></div>
  <div class="brand-band">
    <span class="brand-dot"></span>
    <span class="brand-name">Quorva</span>
  </div>
  <div class="pattern-area pattern-area--bottom" role="img" aria-label="Repeating pattern of small embossed circular brand marks in dark grey"></div>
</section>

<section class="card card--front" aria-label="Card front">
  <div class="brand">
    <span class="brand-dot"></span>
    <span class="brand-name">Quorva</span>
  </div>

  <div class="person">
    <p class="person__name">ADRIEN KOLE</p>
    <p class="person__role">CEO &amp; FOUNDER</p>
  </div>

  <div class="divider"></div>

  <div class="contact">
    <p class="contact__address">4172 Marlowe blvd,<br>Cylver City, CA 90299</p>
    <ul class="contact__list">
      <li>
        <svg viewBox="0 0 24 24" aria-hidden="true"><path d="M6.6 10.8a15.1 15.1 0 0 0 6.6 6.6l2.2-2.2c.3-.3.7-.4 1-.2 1.1.4 2.3.6 3.6.6.6 0 1 .4 1 1V20c0 .6-.4 1-1 1A17 17 0 0 1 3 4c0-.6.4-1 1-1h3.5c.6 0 1 .4 1 1 0 1.3.2 2.5.6 3.6.1.3 0 .7-.2 1z"/></svg>
        <span>555 014 7396</span>
      </li>
      <li>
        <svg viewBox="0 0 24 24" aria-hidden="true"><path d="M2 5h20v14H2z M2 5l10 8 10-8" /></svg>
        <span>yourname@email.com</span>
      </li>
      <li>
        <svg viewBox="0 0 24 24" aria-hidden="true"><circle cx="12" cy="12" r="10"/></svg>
        <span>www.<span class="accent">websitename</span>.com</span>
      </li>
    </ul>
  </div>
</section>

</body>
</html>
```